The design should look similar to the uploaded example to accommodate the information needed for a business card template. I would like to see the colors orange and charcoal grey incorporated along with the logo.The following should be on the back of the card SPECIALIZING IN NEW AND USED TIRES & WHEELS FOR:- Loaders- Skid Steers- Telehandlers- Boom Lifts- Forklifs and moreELIMINATING DOWNTIMEWheel Exchange Program for New & Used Foam Filled and Solid Rubber TiresSPECIALTY SERVICES- Foam Filling Tires- Largest Tire Press in SE- ONSITE Forklift Tire Press- Boom Truck Services - Rubber Tracks

Target Market(s)

New and Existing Customers

Industry/Entity Type

Business

Contact Information for Business Card

NAMEHEAVY DUTY TIRE, LLC8470 Belvedere RoadWest Palm Beach, FL 33411P: 844-HD-TIRESF: 561-431-6469C:E: W: WWW.GRANITERIMSUPPLY-EXAMPLE.COM

Font styles to use
Sans Serif

Colors
f37122
333333

Requirements
Must have
• The logo and the information indicated for the backside of the card
Nice to have
• Keep the orange and charcoal grey colors

```html
<!DOCTYPE html>
<html lang="en">
<head>
<meta charset="utf-8">
<title>Granite Rim Supply – Business Card</title>
<link href="https://fonts.googleapis.com/css2?family=Open+Sans:wght@400;600;700&display=swap" rel="stylesheet">
<style>
  :root{
    --orange:#f37122;
    --orange-soft:#f58a44;
    --charcoal:#333333;
    --slate:#4a5560;
    --paper:#ffffff;
    --backdrop:#e6e6e6;
  }
  *{box-sizing:border-box;margin:0;padding:0}
  html,body{width:1200px;height:900px;overflow:hidden}
  body{background:var(--backdrop);font-family:"Open Sans",Arial,sans-serif;position:relative}

  .card{position:absolute;width:600px;height:343px;background:var(--paper);overflow:hidden;
        box-shadow:0 6px 18px rgba(0,0,0,.18)}

  /* back side */
  .card-back{left:500px;top:70px;border-bottom:4px solid var(--orange);padding:24px 22px 0;text-align:center}
  .card-back h2{color:var(--orange);font-size:17px;font-weight:700;letter-spacing:.2px;text-transform:uppercase;line-height:1.25}
  .card-back h2 + .list{margin-top:8px}
  .card-back .list{color:var(--charcoal);font-size:15.5px;font-weight:600;line-height:1.55}
  .card-back .list span{white-space:nowrap}
  .card-back .dot{display:inline-block;width:7px;height:7px;border-radius:50%;background:var(--orange);margin:0 9px 2px;vertical-align:middle}
  .card-back .section{margin-top:14px}
  .card-back .note{color:var(--charcoal);font-size:15.5px;font-weight:600;line-height:1.35;margin-top:4px}

  /* front side */
  .card-front{left:110px;top:470px}
  .card-front .shape{position:absolute;inset:0}
  .brand{position:absolute;left:26px;top:118px;width:210px;display:flex;align-items:center;gap:10px}
  .brand-dot{width:30px;height:30px;border-radius:50%;background:var(--orange);flex:none}
  .brand-name{color:var(--charcoal);font-size:26px;font-weight:700;line-height:1.05}
  .contact{position:absolute;right:30px;top:30px;text-align:right;color:var(--paper)}
  .contact .person{font-size:23px;font-weight:700;letter-spacing:.4px}
  .contact .company{font-size:18px;font-weight:700;margin-top:6px}
  .contact .address{font-size:16px;line-height:1.35;margin-top:4px}
  .contact ul{list-style:none;margin-top:12px;font-size:16px;line-height:1.5}
  .contact li{display:flex;justify-content:flex-end;align-items:center;gap:9px}
  .contact svg{width:14px;height:14px;flex:none}
</style>
</head>
<body>

<section class="card card-back" aria-label="Card back">
  <h2>Specializing in new and used tires &amp; wheels for</h2>
  <p class="list">
    <span>Loaders</span><i class="dot"></i><span>Skid Steers</span><i class="dot"></i><span>Telehandlers</span><i class="dot"></i><span>Boom Lifts</span><br>
    <span>Forklifs and more</span>
  </p>
  <div class="section">
    <h2>Eliminating downtime</h2>
    <p class="note">Wheel Exchange Program for New &amp; Used Foam<br>Filled and Solid Rubber Tires</p>
  </div>
  <div class="section">
    <h2>Specialty services</h2>
    <p class="list" style="margin-top:4px">
      <span>Foam Filling Tires</span><i class="dot"></i><span>Largest Tire Press in SE</span><br>
      <span>ONSITE Forklift Tire Press</span><i class="dot"></i><span>Boom Truck Services</span><i class="dot"></i><span>Rubber Tracks</span>
    </p>
  </div>
</section>

<section class="card card-front" aria-label="Card front">
  <svg class="shape" viewBox="0 0 600 343" preserveAspectRatio="none" aria-hidden="true">
    <path d="M258 0 C330 60 320 230 190 343 L175 343 C300 230 310 70 238 0 Z" fill="var(--slate)"/>
    <path d="M272 0 L600 0 L600 343 L205 343 C330 240 340 70 272 0 Z" fill="var(--orange-soft)"/>
  </svg>

  <div class="brand">
    <span class="brand-dot"></span>
    <span class="brand-name">GRANITE RIM</span>
  </div>

  <div class="contact">
    <p class="person">Marcus Delaney</p>
    <p class="company">GRANITE RIM SUPPLY, LLC</p>
    <p class="address">5126 Marston Lane<br>Coral Bend, FL 33499</p>
    <ul>
      <li>844-GR-WHEEL
        <svg viewBox="0 0 16 16"><path d="M3 1h3l1.5 4-2 1.3a9 9 0 0 0 4.2 4.2L11 8.5l4 1.5v3a2 2 0 0 1-2 2A13 13 0 0 1 1 3a2 2 0 0 1 2-2z" fill="#fff"/></svg></li>
      <li>561-278-9053
        <svg viewBox="0 0 16 16"><rect x="2" y="5" width="12" height="9" rx="1" fill="#fff"/><rect x="4" y="1" width="8" height="5" fill="#fff"/><rect x="5" y="8" width="6" height="3" fill="var(--orange-soft)"/></svg></li>
      <li>123-456-7890
        <svg viewBox="0 0 16 16"><rect x="3.5" y="1" width="9" height="14" rx="1.5" fill="none" stroke="#fff" stroke-width="1.6"/></svg></li>
      <li>info@granite-example.com
        <svg viewBox="0 0 16 16"><rect x="1" y="3" width="14" height="10" fill="#fff"/><path d="M1 3l7 6 7-6" fill="none" stroke="var(--orange-soft)" stroke-width="1.3"/></svg></li>
      <li>www.graniterimsupply-example.com
        <svg viewBox="0 0 16 16"><circle cx="8" cy="8" r="7" fill="#fff"/><path d="M1 8h14M8 1c3 3 3 11 0 14M8 1c-3 3-3 11 0 14" fill="none" stroke="var(--orange-soft)" stroke-width="1"/></svg></li>
    </ul>
  </div>
</section>

</body>
</html>
```